Design for a real estate wev portal

Contents and features of the site
---------------------------------
Website in 5 languages: French, Dutch, English, German, Spanish.
English name of the site: Harbor Nest Place
Main purpose of the site:
- allow people to rent their house/ appartment for flatsharing purposes.
- help people wanting to find a room in flatsharing
- help people to find additional roommates for their flatsharing
Key interaction sequence:
1. I create a "group" of people who have common interest/hobbies
2. People who have the same interests/hobbies join my group
3. I look for a house/appartment to host my group
Website structure will be the following:
- Home
- Groups
-- Look for a group
--- Join a group
-- Create a group
- Properties
-- Look for a house/appartement
-- Apply
- Sales conditions
- Contact
- My account
-- My profile
-- My groups OR my properties
Your mission
------------
The client has no graphical guidelines, simply a logo (see attached).
We need a (responsive compliant) design for the following pages (we expect PSD's from you. No HTML nor CSS):
1. homepage (see example and wireframe attached)
2. properties search result list (see wireframe attached)
3. "detailed" form for properties
4. groups search result list
5. "detailed" form for groups
6. my account page
FOR THE COMPETITION step we only expect from you the design of first 2 screens.
Based on that, we will select the designer who will win the project, and will have to design the 4 remaining screens.
Target Market(s)
B2C
Industry/Entity Type
Real Estate
Number of Pages Required
5+ page
Look and feel
Each slider illustrates characteristics of the customer's brand and the style your logo design should communicate.

```html
<!DOCTYPE html>
<html lang="en">
<head>
<meta charset="utf-8">
<title>Harbor Nest Place</title>
<link href="https://fonts.googleapis.com/css2?family=Open+Sans:wght@400;600;700&family=Roboto+Condensed:wght@400;700&display=swap" rel="stylesheet">
<style>
:root{
  --green:#6ab23e;
  --green-soft:#acd68e;
  --green-badge:#5cb544;
  --teal:#1aa0b4;
  --teal-badge:#1496aa;
  --teal-link:#178fa3;
  --ink:#333;
  --ink-soft:#666;
  --line:#dcdcdc;
  --footer:#3b3b3b;
  --white:#fff;
}
*{box-sizing:border-box;margin:0;padding:0}
html,body{width:1200px;height:2469px;overflow:hidden}
body{position:relative;background:var(--white);font-family:"Open Sans",sans-serif;color:var(--ink)}
.abs{position:absolute}
.cond{font-family:"Roboto Condensed",sans-serif}

/* header */
.site-header{position:absolute;left:0;top:0;width:1200px;height:113px}
.main-nav a{position:absolute;top:52px;font-size:13px;letter-spacing:.5px;color:var(--ink);text-decoration:none}
.main-nav a.active{color:var(--green)}
.brand{position:absolute;left:512px;top:38px;display:flex;align-items:center;gap:10px;font-family:"Roboto Condensed",sans-serif;font-weight:700;font-size:27px;color:#2f3b33}
.brand-dot{width:18px;height:18px;border-radius:50%;background:var(--green)}
.account-link{position:absolute;left:803px;top:51px;font-size:13px;color:var(--ink)}
.lang-select{position:absolute;left:997px;top:46px;width:104px;height:31px;border:1px solid #ccc;font-size:10px;color:#777;display:flex;align-items:center;padding-left:12px;gap:6px}
.lang-flag{width:16px;height:10px;background:#3b5aa0}

/* hero */
.hero{position:absolute;left:0;top:113px;width:1200px;height:521px;background:linear-gradient(180deg,#6f6a5e 0%,#8a8475 35%,#5f6f3e 70%,#4d7a2a 100%)}
.hero-shade{position:absolute;inset:0;background:rgba(0,0,0,.18)}
.hero-title{position:absolute;left:0;width:1200px;top:230px;text-align:center;color:var(--white);font-family:"Roboto Condensed",sans-serif;font-weight:700;font-size:50px;line-height:1}
.hero-sub{position:absolute;left:0;width:1200px;top:286px;text-align:center;color:var(--white);font-size:20px}
.hero-dots{position:absolute;left:565px;top:326px;display:flex;gap:7px}
.hero-dots span{width:13px;height:13px;border-radius:50%;border:2px solid var(--white)}
.hero-dots span.on{background:var(--white)}

/* choice panels */
.choice-panel{position:absolute;top:591px;width:494px;height:309px;background:var(--green-soft)}
.choice-title{position:absolute;top:22px;left:0;width:100%;text-align:center;font-family:"Roboto Condensed",sans-serif;font-size:20px;color:#2f3a2a}
.choice-card{position:absolute;top:64px;width:222px;height:226px;background:var(--white)}
.choice-photo{height:178px}
.choice-label{height:48px;display:flex;align-items:center;justify-content:center;text-align:center;font-size:12px;line-height:1.3;letter-spacing:.4px;color:#444}

/* spotlight */
.section-heading{position:absolute;font-family:"Roboto Condensed",sans-serif;font-size:22px;color:var(--ink)}
.slider-arrows{position:absolute;top:976px;display:flex;gap:4px}
.slider-arrows span{width:20px;height:20px;border:1px solid #aaa;border-radius:50%;display:flex;align-items:center;justify-content:center}
.spot-card{position:absolute;width:489px;height:189px;border:1px solid var(--line);display:flex}
.spot-photo{width:186px;height:185px;margin:1px}
.spot-body{padding:20px 14px 0 24px;flex:1}
.spot-title{font-size:12.5px;line-height:1.45;color:#444;text-transform:uppercase}
.badge{display:inline-block;margin:10px 0 8px;padding:4px 7px;font-size:11.5px;font-weight:700;color:var(--white)}
.badge.teal{background:var(--teal-badge)}
.badge.green{background:var(--green-badge)}
.spot-lead{font-size:13px;color:#333;margin-bottom:6px}
.spot-text{font-size:11px;line-height:1.8;color:var(--ink-soft)}
.more-link{position:absolute;font-size:12px;font-weight:600;text-decoration:underline;display:flex;align-items:center;gap:4px}

/* selling points */
.selling-band{position:absolute;left:0;top:1531px;width:1200px;height:288px;background:linear-gradient(180deg,#1c9db1 0%,#1aa3b7 60%,#1e9ab3 100%)}
.point-icon{position:absolute;top:76px;width:102px;height:102px;border:3px solid var(--white);border-radius:50%;display:flex;align-items:center;justify-content:center}
.point-title{position:absolute;top:73px;font-family:"Roboto Condensed",sans-serif;font-size:19px;color:var(--white)}
.point-text{position:absolute;top:104px;width:330px;font-size:11.5px;line-height:1.8;color:var(--white)}
.point-link{position:absolute;top:197px;font-size:12px;font-weight:700;color:var(--white);text-decoration:underline}

/* faq */
.faq-heading{position:absolute;left:0;top:1870px;width:1200px;text-align:center;font-family:"Roboto Condensed",sans-serif;font-size:31px;color:#333}
.faq-item{position:absolute;width:460px;height:140px}
.faq-q{position:absolute;left:0;top:0;width:56px;height:56px;border:1px solid #b9dea0;display:flex;align-items:center;justify-content:center;font-weight:700;font-size:22px;color:var(--green)}
.faq-title{position:absolute;left:82px;top:0;font-size:14px;letter-spacing:.4px;color:#333}
.faq-text{position:absolute;left:82px;top:28px;width:380px;font-size:11.5px;line-height:1.8;color:var(--ink-soft)}
.faq-more{position:absolute;left:82px;top:91px;font-size:11px;color:#333}
.all-questions{position:absolute;left:530px;top:2242px;width:140px;height:33px;border:2px solid var(--green);display:flex;align-items:center;justify-content:center;font-size:12px;font-weight:700;color:var(--green);gap:4px}

/* footer */
.site-footer{position:absolute;left:0;top:2326px;width:1200px;height:143px;background:var(--footer);color:var(--white)}
.social-row{position:absolute;left:497px;top:30px;display:flex;gap:6px}
.social-row span{width:30px;height:30px;border:2px solid var(--white);border-radius:50%}
.footer-links{position:absolute;left:0;top:71px;width:1200px;text-align:center;font-size:12.5px}
.footer-links a{color:var(--white);text-decoration:underline}
.copyright{position:absolute;left:0;top:98px;width:1200px;text-align:center;font-size:12.5px}
</style>
</head>
<body>

<header class="site-header">
  <nav class="main-nav">
    <a class="active" style="left:99px" href="#">HOME</a>
    <a style="left:174px" href="#">ABOUT US</a>
    <a style="left:278px" href="#">SERVICES</a>
    <a style="left:379px" href="#">CONTACT US</a>
  </nav>
  <div class="brand"><span class="brand-dot"></span>Harbor Nest Place</div>
  <div class="account-link">Create / Login / My Account</div>
  <div class="lang-select"><span class="lang-flag"></span>ENGLISH
    <svg width="10" height="6" viewBox="0 0 10 6" style="margin-left:8px"><path d="M1 1l4 4 4-4" fill="none" stroke="#888" stroke-width="1.2"/></svg>
  </div>
</header>

<section class="hero" role="img" aria-label="Photo of a suburban family house with a green lawn">
  <div class="hero-shade"></div>
  <h1 class="hero-title">HARBOR NEST PLACE</h1>
  <p class="hero-sub">Sed ut perspiciatis unde omnis iste</p>
  <div class="hero-dots"><span class="on"></span><span></span><span></span><span></span></div>
</section>

<section class="choice-panel" style="left:99px">
  <h2 class="choice-title">SEARCHING FOR ACCOMMODATION</h2>
  <div class="choice-card" style="left:16px">
    <div class="choice-photo" role="img" aria-label="Photo of a cosy bedroom" style="background:linear-gradient(135deg,#c9a06a,#6d4a2c)"></div>
    <div class="choice-label">I WANT TO RENT A ROOM<br>RIGHT NOW !</div>
  </div>
  <div class="choice-card" style="left:255px">
    <div class="choice-photo" role="img" aria-label="Photo of people meeting at a reception desk" style="background:linear-gradient(135deg,#8fa6b8,#9a5a3a)"></div>
    <div class="choice-label">I WANT TO JOIN<br>A GROUP</div>
  </div>
</section>

<section class="choice-panel" style="left:606px">
  <h2 class="choice-title">I HAVE A HOUSE FOR RENT</h2>
  <div class="choice-card" style="left:14px">
    <div class="choice-photo" role="img" aria-label="Photo of a host welcoming a guest at a desk" style="background:linear-gradient(135deg,#3a3028,#a07a4a)"></div>
    <div class="choice-label">I WANT TO<br>ADVERTISE !</div>
  </div>
  <div class="choice-card" style="left:254px">
    <div class="choice-photo" role="img" aria-label="Photo of a warmly lit hotel bedroom" style="background:linear-gradient(135deg,#3a1e14,#9a4a2a)"></div>
    <div class="choice-label">WHY IS FLATSHARING<br>INTERESTING FOR ME ?</div>
  </div>
</section>

<h2 class="section-heading" style="left:99px;top:973px">UNDER THE SPOTLIGHT</h2>
<div class="slider-arrows" style="left:545px">
  <span><svg width="8" height="8" viewBox="0 0 8 8"><path d="M5 1L2 4l3 3" fill="none" stroke="#888" stroke-width="1.2"/></svg></span>
  <span><svg width="8" height="8" viewBox="0 0 8 8"><path d="M3 1l3 3-3 3" fill="none" stroke="#888" stroke-width="1.2"/></svg></span>
</div>
<h2 class="section-heading" style="left:610px;top:973px">UNDER THE SPOTLIGHT</h2>
<div class="slider-arrows" style="left:1057px">
  <span><svg width="8" height="8" viewBox="0 0 8 8"><path d="M5 1L2 4l3 3" fill="none" stroke="#888" stroke-width="1.2"/></svg></span>
  <span><svg width="8" height="8" viewBox="0 0 8 8"><path d="M3 1l3 3-3 3" fill="none" stroke="#888" stroke-width="1.2"/></svg></span>
</div>

<article class="spot-card" style="left:99px;top:1029px">
  <div class="spot-photo" role="img" aria-label="Photo of a group of young professionals" style="background:linear-gradient(135deg,#d8d8d8,#3a3a3a)"></div>
  <div class="spot-body">
    <div class="spot-title">A nice group young workers, seeking<br>for accomodation downtown.</div>
    <span class="badge teal">AVERAGE AGE: 35 Y</span>
    <div class="spot-lead">Men and women welcome</div>
    <div class="spot-text">Nulla at diam ornare, aliquam urna vel, commodo urna. Nam id risus a est luctus consectetur</div>
  </div>
</article>
<article class="spot-card" style="left:99px;top:1234px">
  <div class="spot-photo" role="img" aria-label="Photo of students looking at a tablet together" style="background:linear-gradient(135deg,#8fa8c8,#2c3c58)"></div>
  <div class="spot-body" style="padding-top:20px">
    <div class="spot-title">Aonther nice group young ladies,<br>studying at university seeking for<br>&nbsp;accomodation close to Brussels<br>university.</div>
    <span class="badge teal" style="margin-top:6px">AVERAGE AGE: 20 Y</span>
    <div class="spot-lead">Olny women</div>
  </div>
</article>
<a class="more-link" style="left:462px;top:1445px;color:var(--teal-link)">SEE MORE GROUPS
  <svg width="10" height="10" viewBox="0 0 10 10"><circle cx="5" cy="5" r="4" fill="none" stroke="currentColor"/><path d="M4 3l2 2-2 2" fill="none" stroke="currentColor"/></svg></a>

<article class="spot-card" style="left:610px;top:1029px">
  <div class="spot-photo" role="img" aria-label="Photo of a modern two-storey house at dusk" style="background:linear-gradient(180deg,#5a78b8,#9a9aa0 60%,#6a6a6a)"></div>
  <div class="spot-body">
    <div class="spot-title">House town.<br>Rent per month</div>
    <span class="badge green">AVAILABILITY</span>
    <div class="spot-text">Sed ut perspiciatis unde omnis iste natus error sit voluptatem accusantium doloremque laudantium, totam rem aperiam, eaque ipsa quae</div>
  </div>
</article>
<article class="spot-card" style="left:610px;top:1234px">
  <div class="spot-photo" role="img" aria-label="Photo of a house with a garden and lawn" style="background:linear-gradient(180deg,#8fb8e0,#8a9a7a 55%,#4a8a2a)"></div>
  <div class="spot-body">
    <div class="spot-title">House town.<br>Rent per month</div>
    <span class="badge green">AVAILABILITY</span>
    <div class="spot-text">Sed ut perspiciatis unde omnis iste natus error sit voluptatem accusantium doloremque laudantium, totam rem aperiam, eaque ipsa quae</div>
  </div>
</article>
<a class="more-link" style="left:975px;top:1445px;color:var(--green)">SEE MORE HOUSES
  <svg width="10" height="10" viewBox="0 0 10 10"><circle cx="5" cy="5" r="4" fill="none" stroke="currentColor"/><path d="M4 3l2 2-2 2" fill="none" stroke="currentColor"/></svg></a>

<section class="selling-band" aria-label="Key selling points">
  <div class="point-icon" style="left:99px">
    <svg width="52" height="52" viewBox="0 0 52 52"><path d="M6 8h18l22 22-16 16L8 24z" fill="#fff" transform="rotate(0)"/><circle cx="15" cy="17" r="3.5" fill="#1aa0b4"/></svg>
  </div>
  <h3 class="point-title" style="left:219px">KEY SELLING POINTS FOR THE ROOMMATES</h3>
  <p class="point-text" style="left:219px">Sed ut perspiciatis unde omnis iste natus error sit voluptatem accusantium doloremque laudantium, totam rem aperiam, eaque ipsa quae ab illo inventore veritatis et quasi architecto beatae vitae dicta sunt explicabo.</p>
  <a class="point-link" style="left:217px">SEE MORE ⊙</a>

  <div class="point-icon" style="left:650px">
    <svg width="44" height="48" viewBox="0 0 44 48"><circle cx="22" cy="13" r="11" fill="#fff"/><path d="M3 46c0-12 8-19 19-19s19 7 19 19z" fill="#fff"/></svg>
  </div>
  <h3 class="point-title" style="left:769px">KEY SELLING POINTS FOR THE OWNERS</h3>
  <p class="point-text" style="left:769px">Sed ut perspiciatis unde omnis iste natus error sit voluptatem accusantium doloremque laudantium, totam rem aperiam, eaque ipsa quae ab illo inventore veritatis et quasi architecto beatae vitae dicta sunt explicabo.</p>
  <a class="point-link" style="left:769px">SEE MORE ⊙</a>
</section>

<h2 class="faq-heading">EVERYTHING YOU NEED TO KNOW ABOUT FLATSHARING</h2>

<div class="faq-item" style="left:99px;top:1964px">
  <div class="faq-q">Q</div>
  <h4 class="faq-title">WHERE DOES IT COME FROM?</h4>
  <p class="faq-text">Sed ut perspiciatis unde omnis iste natus error sit voluptatem accusantium doloremque laudantium, totam rem aperiam, eaque ipsa quae ab illo inventore veritatis et quasi architecto beatae</p>
  <a class="faq-more">READ MORE ⊙</a>
</div>
<div class="faq-item" style="left:637px;top:1964px">
  <div class="faq-q">Q</div>
  <h4 class="faq-title">WHERE DOES IT COME FROM?</h4>
  <p class="faq-text">Sed ut perspiciatis unde omnis iste natus error sit voluptatem accusantium doloremque laudantium, totam rem aperiam, eaque ipsa quae ab illo inventore veritatis et quasi architecto beatae</p>
  <a class="faq-more">READ MORE ⊙</a>
</div>
<div class="faq-item" style="left:99px;top:2110px">
  <div class="faq-q">Q</div>
  <h4 class="faq-title">WHERE DOES IT COME FROM?</h4>
  <p class="faq-text">Sed ut perspiciatis unde omnis iste natus error sit voluptatem accusantium doloremque laudantium, totam rem aperiam, eaque ipsa quae ab illo inventore veritatis et quasi architecto beatae</p>
  <a class="faq-more">READ MORE ⊙</a>
</div>
<div class="faq-item" style="left:637px;top:2110px">
  <div class="faq-q">Q</div>
  <h4 class="faq-title">WHERE DOES IT COME FROM?</h4>
  <p class="faq-text">Sed ut perspiciatis unde omnis iste natus error sit voluptatem accusantium doloremque laudantium, totam rem aperiam, eaque ipsa quae ab illo inventore veritatis et quasi architecto beatae</p>
  <a class="faq-more">READ MORE ⊙</a>
</div>

<a class="all-questions">ALL QUESTION ⊙</a>

<footer class="site-footer">
  <div class="social-row"><span></span><span></span><span></span><span></span><span></span><span></span></div>
  <p class="footer-links"><a>Pre-defined Searches</a> &nbsp;/ <a>Tools And Informations</a></p>
  <p class="copyright">Copyright @ 2016 Harbor Nest Place. All Rights Reserved.</p>
</footer>

</body>
</html>
```